Business Cards Design for the electrical wholesaler: clean bold dynamic :)

We need a business card design that would follow our latest brand guidelines. As an electrical wholesaler we want to bring a fresh look and feel into the industry. The design should be clean bold and dynamic. It should come alive with the renewed energy of our green colour. Our grey colour should keep things balanced and complement the notion of maturity and responsibility. We employ Lato as a corporate font however are not bound by this font and we’re open to interpretation here.

Target Market(s)

Electrical contractors

Industry/Entity Type

Business

Contact Information for Business Card

Logo
Name & Surname: Halyna Dorosh
Job Title: Director of Marketing
Email: halya.dorosh@quillmail.example
Cell phone: XXX.XXX.XXXX
Address: 20517 - 87 Ave. Edmonton, AB, Canada. T6K 4N8
Business Phone: 780.555.0184
Website: www.brovix.example

Font styles to use
Other font styles liked:
• Lato

Requirements
Must have
• Logo & website
Nice to have
• Brand elements - some of them you may find in the attached Brand Guidelines (e.g. three lines on the background signifying "W")

```html
<!DOCTYPE html>
<html lang="en">
<head>
<meta charset="utf-8">
<title>Brovix business card</title>
<link href="https://fonts.googleapis.com/css2?family=Lato:wght@400;700&display=swap" rel="stylesheet">
<style>
  :root {
    --green: #86bd3b;
    --grey: #505154;
    --text-grey: #4a4b4d;
    --card-white: #f5f5f4;
    --backdrop: #c9c9c9;
    --rule: #bdbdbd;
  }
  * { margin: 0; padding: 0; box-sizing: border-box; }
  html, body {
    width: 1200px; height: 960px; overflow: hidden;
    background: var(--backdrop);
    font-family: "Lato", Arial, sans-serif;
  }
  .stage { position: relative; width: 1200px; height: 960px; }

  .card { position: absolute; left: 320px; width: 600px; }

  /* Front */
  .card-front {
    top: 100px; height: 348px;
    background: var(--green);
  }
  .front-brand {
    position: absolute; left: 0; right: 0; top: 128px;
    display: flex; justify-content: center; align-items: center; gap: 14px;
    color: #ffffff; font-weight: 700; font-size: 64px; line-height: 1;
  }
  .brand-dot { width: 22px; height: 22px; border-radius: 50%; background: #ffffff; }
  .front-web {
    position: absolute; left: 0; right: 0; top: 300px;
    text-align: center; color: #ffffff;
    font-size: 13px; letter-spacing: 3.2px;
  }

  /* Back */
  .card-back {
    top: 493px; height: 344px;
    background: var(--card-white);
  }
  .back-brand {
    position: absolute; left: 80px; top: 150px;
    display: flex; align-items: center; gap: 12px;
    color: var(--grey); font-weight: 400; font-size: 54px; line-height: 1;
  }
  .back-brand .brand-dot { background: var(--green); width: 20px; height: 20px; }
  .divider {
    position: absolute; left: 308px; top: 76px; width: 1px; height: 196px;
    background: var(--rule);
  }
  .details { position: absolute; left: 346px; top: 74px; color: var(--text-grey); }
  .person-name { color: var(--green); font-weight: 700; font-size: 19px; line-height: 22px; }
  .person-title { font-size: 15px; line-height: 20px; text-transform: uppercase; }
  .address { margin-top: 10px; font-size: 14px; line-height: 19px; width: 230px; }
  .contacts { list-style: none; margin-top: 10px; font-size: 14px; line-height: 19px; }
  .contacts li { display: flex; align-items: center; gap: 9px; }
  .contacts svg { width: 13px; height: 13px; fill: var(--green); flex: none; }

  .card-band { position: absolute; left: 0; bottom: 0; width: 600px; height: 15px; }
</style>
</head>
<body>
<main class="stage">

  <section class="card card-front" aria-label="Card front">
    <div class="front-brand"><span class="brand-dot"></span><span>brovix</span></div>
    <p class="front-web">www.brovix.example</p>
  </section>

  <section class="card card-back" aria-label="Card back">
    <div class="back-brand"><span class="brand-dot"></span><span>brovix</span></div>
    <div class="divider"></div>
    <div class="details">
      <p class="person-name">HALYNA DOROSH</p>
      <p class="person-title">CEO/Founder</p>
      <p class="address">20517 - 87 Ave. Edmonton, AB, Canada. T6K 4N8</p>
      <ul class="contacts">
        <li><svg viewBox="0 0 16 16"><path d="M3.5 1l3 3-1.6 2a9 9 0 0 0 5.1 5.1l2-1.6 3 3-1.8 2C7 14.5 1.5 9 1.5 2.8z"/></svg>780.555.0184</li>
        <li><svg viewBox="0 0 16 16"><path d="M4.5 0h7a1 1 0 0 1 1 1v14a1 1 0 0 1-1 1h-7a1 1 0 0 1-1-1V1a1 1 0 0 1 1-1zm.6 2v10h5.8V2zM8 13a1 1 0 1 0 0 2 1 1 0 0 0 0-2z"/></svg>780.555.0127</li>
        <li><svg viewBox="0 0 16 16"><path d="M4 1h8v4H4zM1 6h14v6h-2v3H3v-3H1zm4 4v3h6v-3z"/></svg>780.555.0193</li>
        <li><svg viewBox="0 0 16 16"><path d="M1 3h14v10H1zm1.5 1.5L8 9l5.5-4.5z"/></svg>halya.dorosh@quillmail.example</li>
        <li><svg viewBox="0 0 16 16"><path d="M8 1a7 7 0 1 0 0 14A7 7 0 0 0 8 1zm-1 2.2v2.3L5 7v2l2 1.5V13a5 5 0 0 1-3.9-6.5zm2 9.7V10l2-1.5L12.5 10A5 5 0 0 1 9 12.9zm3.8-4.9L11 6.5 9 6V3.2A5 5 0 0 1 12.8 8z"/></svg>www.brovix.example</li>
      </ul>
    </div>
    <svg class="card-band" viewBox="0 0 600 15" aria-hidden="true">
      <polygon points="0,0 392,0 388,15 0,15" fill="var(--green)"/>
      <polygon points="398,0 600,0 600,15 394,15" fill="var(--grey)"/>
    </svg>
  </section>

</main>
</body>
</html>
```